E-Commerce Web Design Project - Online Designer Childrens Clothing

I currently have a website at http://qrk.example/Tm4vRa but I am not happy with the look and feel. I mainly want black and white colours as my images will have splashes of colour

I am going for a complete new look and will require the following:

1. Home page - to have categories listed on the left side bar and large scrolling images in the center (600px by 450px) with 3 static boxes equally spaced underneath (325px by 142px) so that I can change them to different links. 3 static boxes to be on the right side bar in vertical position each size (198px by 145px).

2. category pages - to have image across the width of the page for my category title page eg. Marbury's kids. category pages to have 3 products across and ability to view all or go down to the page fold.

3. product Details pages - product image to be on the left side bar. All drop down boxes to be of equal size in width and length. Other products you may like is to be removed. Please see the following links as to what I would like it to look like layout wise http://qrk.example/Wp7dGs

4. All other pages such as the Contact us, T's and C's, About Us, Ordering and Delivery etc to have the same template where I will be able to keep adding pages as I need to.

I will be transferring my services to Tillvane and will seek a web developer once the design is confirmed.

3 websites that i love are the following:
http://qrk.example/Wp7dGs
http://qrk.example/Bz2fUe
http://qrk.example/3JtYon
http://qrk.example/gumaLQ

I want my website to be sleek and modern and have a fashion magazine feel to it. the layout is to be clean with everything in proportion. I already have my logo in greyscale that I have attached it to this project.

Please let me know if you have further questions.
Updates

would love to see more designs!i have added a couple more logo files also to add.

Reason: I have now guaranteed tthis project so hopefully more designs will come through!!

I have now guranteed this project so would love to see a few more designs!!!

Reason: I need time to review all submissions and request changes if need be

Target Market(s)

women 25-45 on good disposable income who like their designer brands and love to dress their boys in them

Industry/Entity Type

Fashion

Requirements
Must have
• must be easy to navigate and not to busy. nice and sleek with a fashion magazine feel to it. want it to be more monotone in black and white as my images will add colour
Nice to have
• I love the look of the following websites.

Home Pages:
http://qrk.example/3JtYon
http://qrk.example/Bz2fUe
http://qrk.example/hRN8T4
http://qrk.example/wiDk2v
http://qrk.example/Ezm5o
http://qrk.example/xTcHoa
http://qrk.example/P3sRyd

Category Page:

Product Details Page:
http://qrk.example/Wp7dGs
http://qrk.example/NuqaWt
http://qrk.example/RfzvIm

Products details page:
http://qrk.example/G6WJ9k
http://qrk.example/Wp7dGs

Should not have
• I do not want any quirky or childlike illustrations or the colorful blue. this website is for boys clothing but it targeted at women!!

```html
<!DOCTYPE html>
<html lang="en">
<head>
<meta charset="utf-8">
<title>Brightlad Wear – Home</title>
<link href="https://fonts.googleapis.com/css2?family=Open+Sans:wght@400;600;700&display=swap" rel="stylesheet">
<style>
:root{
  --ink:#222;
  --ink-soft:#555;
  --panel:#262626;
  --panel-edge:#3a3a3a;
  --line:#d6d6d6;
  --paper:#fff;
  --mist:#f2f2f2;
  --price:#f5c400;
  --muted:#888;
}
*{box-sizing:border-box;margin:0;padding:0}
html,body{width:1108px;height:1200px;overflow:hidden}
body{position:relative;background:var(--paper);font-family:"Open Sans",Arial,sans-serif;color:var(--ink)}
a{color:inherit;text-decoration:none}
.abs{position:absolute}

/* utility bar */
.utility-bar{left:0;top:0;width:1108px;height:39px;background:linear-gradient(#fdfdfd,#ececec);border-bottom:2px solid #d2d2d2}
.utility-links{position:absolute;right:100px;top:11px;font-size:12px;color:#444;display:flex;align-items:center;gap:7px}
.utility-links .sep{color:#999}
.chat-icon{width:18px;height:15px;background:#b9b9b9;border-radius:2px;display:inline-block}
.flag{width:18px;height:12px;background:linear-gradient(135deg,#1d2f80,#2b43a8);display:inline-block}

/* header */
.brand{left:92px;top:68px;width:240px;display:flex;align-items:center;gap:10px}
.brand-mark{width:18px;height:18px;background:#555}
.brand-name{font-size:27px;font-weight:600;color:#555;letter-spacing:3px;line-height:1}
.search{left:674px;top:96px;width:332px;height:28px;border:1px solid #c8c8c8;border-radius:3px;background:linear-gradient(#f3f3f3,#fff);display:flex}
.search span{flex:1;font-size:12px;font-style:italic;color:#999;padding:5px 10px;letter-spacing:.5px}
.search-btn{width:42px;height:26px;background:linear-gradient(#5a5a5a,#2e2e2e);border-radius:0 2px 2px 0;display:flex;align-items:center;justify-content:center}

/* main nav */
.main-nav{left:84px;top:144px;width:922px;height:42px;background:linear-gradient(#4a4a4a,#1f1f1f);border-radius:4px;display:flex;color:#fff;font-size:14px}
.main-nav a{padding:0 21px;line-height:42px;border-right:1px solid #111;box-shadow:1px 0 0 #555}
.main-nav a:first-child{padding:0 28px}
.bag{margin-left:auto;display:flex;align-items:center;gap:8px;padding-right:14px;font-size:13px}
.bag b{font-weight:700}
.bag small{font-size:12px;color:#ddd}

/* shop sidebar */
.shop{left:84px;top:198px;width:172px;height:415px;border:1px solid var(--line)}
.shop h2{background:#1f1f1f;color:#fff;font-size:16px;font-weight:700;height:34px;line-height:34px;padding-left:13px}
.shop ul{list-style:none;padding:1px 0 0 1px}
.shop li{height:33px;border-bottom:1px solid #e3e3e3;font-size:11.5px;color:#333;line-height:33px;padding-left:14px;margin-right:1px}
.shop li:last-child{border-bottom:0}
.shop li::before{content:"›";color:#666;margin-right:10px}

/* hero slider */
.hero{left:261px;top:197px;width:557px;height:416px;border:1px solid var(--line);padding:5px}
.hero-image{width:100%;height:100%;background:radial-gradient(circle at 55% 45%,#8a8a90 0%,#6e5560 35%,#7a4a58 70%,#6a3a48 100%)}
.dots{position:absolute;left:15px;bottom:14px;display:flex;gap:8px}
.dots i{width:34px;height:34px;border-radius:50%;background:rgba(255,255,255,.45);display:block}
.dots i.on{background:#222;border:6px solid #fff}

/* side products */
.side-product{left:823px;width:184px;height:135px;border:1px solid var(--line);background:#fff}
.side-product .name{position:absolute;left:10px;top:32px;font-size:12px;font-weight:600;line-height:15.5px;width:70px;z-index:1}
.side-product .rrp{display:block;font-weight:400;text-decoration:line-through;color:#555}
.side-product .thumb{position:absolute;right:2px;top:6px;width:100px;height:92px}
.side-product .bar{position:absolute;left:0;bottom:0;width:100%;height:30px;background:#1f1f1f;color:#fff;display:flex;justify-content:space-between;align-items:center;padding:0 8px 0 10px;font-size:13px}
.side-product .bar b{color:var(--price);font-weight:700}

/* promo tiles */
.promo{top:623px;width:299px;height:130px;background:var(--panel);color:#fff}
.promo .disc{position:absolute;left:7px;top:4px;width:123px;height:123px;border-radius:50%;background:#fff;border:3px solid #ddd;padding:8px}
.promo .disc div{width:100%;height:100%;border-radius:50%}
.promo h3{position:absolute;left:143px;top:10px;font-size:21px;font-weight:400;line-height:28px;letter-spacing:.5px}
.promo .cta{position:absolute;left:144px;top:100px;font-size:13.5px}

/* brands */
.brands{left:84px;top:763px;width:922px;height:116px;border:1px solid var(--line)}
.brands h2{font-size:17px;font-weight:600;position:absolute;left:13px;top:12px}
.brand-row{position:absolute;left:14px;top:51px;display:flex;gap:18px}
.brand-row div{width:133px;height:47px;border:1px solid var(--line);display:flex;align-items:center;justify-content:center;font-size:17px;font-weight:600;color:#444}

/* about + newsletter */
.about{left:84px;top:896px;width:630px}
.about h2{font-size:17px;font-weight:600;margin-bottom:6px}
.about p{font-size:11.3px;line-height:18.5px;color:#555}
.newsletter{left:738px;top:899px;width:268px;height:121px;border:1px solid var(--line);padding:10px 14px}
.newsletter h2{font-size:17px;font-weight:600;margin-bottom:12px}
.newsletter .field{height:28px;border:1px solid #c8c8c8;border-radius:4px;background:linear-gradient(#f0f0f0,#fff);font-size:12px;font-style:italic;color:#999;padding:5px 10px;letter-spacing:.5px}
.newsletter .btn{position:absolute;right:20px;top:82px;width:77px;height:28px;border-radius:4px;background:linear-gradient(#6a6a6a,#3a3a3a);color:#fff;font-size:13.5px;font-weight:600;text-align:center;line-height:28px}

/* footer */
.footer{left:0;top:1035px;width:1108px;height:165px;background:#262626;color:#fff}
.footer .col{position:absolute;top:18px}
.footer h4{font-size:13.5px;font-weight:600;margin-bottom:8px}
.footer li{list-style:none;font-size:12px;line-height:23.5px;color:#eee}
.social li{display:flex;align-items:center;gap:10px;line-height:28px}
.social i{width:15px;height:15px;border-radius:50%;background:#ddd;display:block}
.cards{display:flex;gap:3px}
.cards i{width:30px;height:20px;border-radius:2px;background:#9a9a9a;display:block}
.cards i:nth-child(2){background:#bdbdbd}
.cards i:nth-child(3){background:#8fa3b8}
.cards i:nth-child(4){background:#c9c9c9}
.foot-brand{left:766px;top:20px;font-size:27px;font-weight:600;color:#bdbdbd;letter-spacing:3px;display:flex;align-items:center;gap:10px}
.foot-brand i{width:18px;height:18px;background:#bdbdbd;display:block}
.legal{left:766px;top:112px;font-size:12px;line-height:19.5px;color:#eee}
</style>
</head>
<body>

<div class="abs utility-bar">
  <nav class="utility-links">
    <a>Live Chat</a><span class="chat-icon" role="img" aria-label="chat icon"></span>
    <span class="sep">|</span><a>AU</a><span class="flag" role="img" aria-label="Australian flag"></span><a>0400 123 987</a>
    <span class="sep">|</span><a>Wishlist</a>
    <span class="sep">|</span><a>My account</a>
    <span class="sep">|</span><a>Contact</a>
    <span class="sep">|</span><a>Shipping</a>
    <span class="sep">|</span><a>FAQ</a>
    <span class="sep">|</span><a>Newsletter</a>
    <span class="sep">|</span><a>Blog</a>
    <span class="sep">|</span><a>Press</a>
    <span class="sep">|</span><a>Login</a>
  </nav>
</div>

<header>
  <div class="abs brand"><i class="brand-mark"></i><span class="brand-name">BRIGHTLAD WEAR</span></div>
  <div class="abs search">
    <span>Search entire store</span>
    <div class="search-btn">
      <svg width="22" height="20" viewBox="0 0 22 20"><circle cx="8" cy="8" r="6" fill="none" stroke="#fff" stroke-width="2.5"/><line x1="12.5" y1="12.5" x2="19" y2="18" stroke="#fff" stroke-width="3.5" stroke-linecap="round"/></svg>
    </div>
  </div>
</header>

<nav class="abs main-nav">
  <a>Home</a><a>About Us</a><a>Blog</a><a>Sizing</a><a>Media</a><a>Contact Us</a><a style="border:0;box-shadow:none">Login</a>
  <div class="bag">
    <svg width="32" height="26" viewBox="0 0 32 26"><path d="M9 10 L16 2 L23 10" fill="none" stroke="#fff" stroke-width="2"/><path d="M2 10 H30 L26 25 H6 Z" fill="#fff"/><path d="M10 14 V21 M16 14 V21 M22 14 V21" stroke="#333" stroke-width="1.5"/></svg>
    <b>MY BAG</b><small>AU $0.00</small>
  </div>
</nav>

<aside class="abs shop">
  <h2>SHOP</h2>
  <ul>
    <li>T Shirts And Tops</li>
    <li>Shirts And Jumpers</li>
    <li>Pants And Shorts</li>
    <li>Jeans</li>
    <li>Jackets and Coats</li>
    <li>Beachwear</li>
    <li>Sleepwear</li>
    <li>Shoes and Socks</li>
    <li>Accessories</li>
    <li>Bags &amp; Luggages</li>
    <li>Gift Certificates</li>
  </ul>
</aside>

<section class="abs hero">
  <div class="hero-image" role="img" aria-label="Boy in a flat cap and striped scarf against a dusky rose backdrop"></div>
  <div class="dots"><i class="on"></i><i></i><i></i></div>
</section>

<article class="abs side-product" style="top:197px">
  <div class="name">Library/ Swim Bag Dinosaur</div>
  <div class="thumb" role="img" aria-label="Green drawstring swim bag" style="background:linear-gradient(150deg,#3b5a3a,#6e9a3a)"></div>
  <div class="bar"><b>AU$24.95</b><span>Details ›</span></div>
</article>
<article class="abs side-product" style="top:339px">
  <div class="name">Marbury's Kids Shorts<span class="rrp">RRP: $59.95</span></div>
  <div class="thumb" role="img" aria-label="Kids denim shorts on a hanger" style="background:linear-gradient(#2f4a66,#1f3348)"></div>
  <div class="bar"><b>AU$30.00</b><span>Details ›</span></div>
</article>
<article class="abs side-product" style="top:479px">
  <div class="name">Marbury's Kids T-Shirt Cans<span class="rrp">RRP: $39.95</span></div>
  <div class="thumb" role="img" aria-label="White kids t-shirt with a printed graphic" style="background:radial-gradient(circle at 60% 50%,#8a8a8a 0 18%,#f4f4f4 20%)"></div>
  <div class="bar"><b>AU$19.95</b><span>Details ›</span></div>
</article>

<a class="abs promo" style="left:84px">
  <div class="disc"><div role="img" aria-label="Green patterned pencil case" style="background:linear-gradient(160deg,#2c4a30,#6b8f3a)"></div></div>
  <h3>ACCESSORIES</h3><span class="cta">Shop Now &nbsp;›</span>
</a>
<a class="abs promo" style="left:396px">
  <div class="disc"><div role="img" aria-label="Red t-shirt and patterned shorts" style="background:linear-gradient(#d8262b 0 50%,#2a2238 50%)"></div></div>
  <h3>KIDS<br>CLOTHES</h3><span class="cta">Shop Now &nbsp;›</span>
</a>
<a class="abs promo" style="left:708px">
  <div class="disc"><div role="img" aria-label="Printed gift certificate" style="background:linear-gradient(#f4f4f4 0 30%,#555 30% 45%,#f4f4f4 45%)"></div></div>
  <h3>GIFTS<br>CERTIFICATES</h3><span class="cta">Shop Now &nbsp;›</span>
</a>

<section class="abs brands">
  <h2>FEATURED BRANDS</h2>
  <div class="brand-row">
    <div>Hollin &amp; Reed</div>
    <div>Stanwick</div>
    <div>pennyloft</div>
    <div>Orvane</div>
    <div>Dunmore</div>
    <div>Ashcroft</div>
  </div>
</section>

<section class="abs about">
  <h2>ABOUT US</h2>
  <p>So your little boy is turning into a little man and you're finding it extremely difficult to find fashionable clothes to help him develop his own sense of style. You are not alone! With the multitude of kid's clothing stores all catering mainly to little girls, parents of boys in their "tween-age" years (8 to 14 years old) obviously have their work cut out for them. Having done considerable research, I discovered that clothes in children's wear departments were either to small or clothes in men's stores were to big!! There was no inbetween!!</p>
</section>

<section class="abs newsletter">
  <h2>SIGN UP FOR NEWSLETTER</h2>
  <div class="field">enter email address</div>
  <div class="btn">Subscribe</div>
</section>

<footer class="abs footer">
  <div class="col" style="left:84px"><h4>Customer Services</h4><ul><li>Contact</li><li>FAQ</li><li>Shipping</li><li>Size Guide</li><li>Trust Policy</li></ul></div>
  <div class="col" style="left:266px"><h4>About</h4><ul><li>Careers</li><li>Testimonials</li><li>Press</li><li>Affiliate Program</li><li>Terms/Conditions</li></ul></div>
  <div class="col social" style="left:425px"><h4>Join Us on</h4><ul><li><i></i>Friendsheet</li><li><i></i>Chirper</li><li><i></i>Circleplus</li></ul></div>
  <div class="col" style="left:577px"><h4>Payment Method</h4><div class="cards"><i></i><i></i><i></i><i></i></div></div>
  <div class="abs foot-brand"><i></i>BRIGHTLAD WEAR</div>
  <div class="abs legal">©2012 brightladwear.example<br>All rights reserved | &nbsp;Privacy</div>
</footer>

</body>
</html>
```